"Jewelry Line Postcard Design"

Would like to describe what the line is about via a bio include a photo of me and the logo.

Target Market(s)

20-55

Industry/Entity Type

Jewelry

```html
<!DOCTYPE html>
<html lang="en">
<head>
<meta charset="utf-8">
<title>Solene Vara – Jewelry Line Postcard</title>
<link rel="stylesheet" href="https://fonts.googleapis.com/css2?family=Cinzel:wght@400;600&family=PT+Sans:wght@400;700&family=PT+Sans+Narrow:wght@700&display=swap">
<style>
  :root {
    --backdrop: #2a2a2a;
    --card: #ffffff;
    --ink: #1c1c1c;
    --magenta: #c8338f;
    --band: #cf6fa8;
    --band-fade: rgba(207,111,168,0);
    --stamp: #f1e1ef;
    --photo-dark: #3a3a3a;
    --photo-mid: #9a9a9a;
    --photo-light: #e6e6e6;
  }
  * { box-sizing: border-box; margin: 0; padding: 0; }
  html, body { width: 1200px; height: 1000px; overflow: hidden; }
  body {
    position: relative;
    background: var(--backdrop);
    font-family: "PT Sans", Arial, sans-serif;
    color: var(--ink);
  }
  .postcard { position: absolute; background: var(--card); overflow: hidden; }

  /* ---------- back side ---------- */
  .postcard--back { left: 48px; top: 53px; width: 623px; height: 482px; }
  .back-portrait {
    position: absolute; inset: 0;
    background:
      radial-gradient(ellipse 40% 55% at 45% 25%, rgba(215,200,190,.45), rgba(255,255,255,0) 70%),
      linear-gradient(180deg, #f4f0ef 0%, #fbfafa 60%, #ffffff 100%);
  }
  .stamp-box {
    position: absolute; left: 479px; top: 27px;
    width: 111px; height: 116px; background: var(--stamp);
  }
  .brand-mark {
    position: absolute; display: flex; align-items: center; gap: 6px;
    font-family: "PT Sans", Arial, sans-serif; font-weight: 400;
    color: var(--ink); letter-spacing: .08em; text-transform: uppercase;
  }
  .brand-mark__dot { width: 7px; height: 7px; background: var(--magenta); }
  .postcard--back .brand-mark { left: 34px; top: 150px; font-size: 15px; }
  .back-bio {
    position: absolute; left: 34px; top: 192px; width: 268px;
    font-size: 14px; line-height: 19px;
  }
  .name-band {
    position: absolute; left: 0; height: 25px; padding-left: 34px;
    background: linear-gradient(90deg, var(--band) 0%, var(--band) 70%, var(--band-fade) 100%);
    font-family: "PT Sans Narrow", "Arial Narrow", sans-serif; font-weight: 700;
    color: #fff; font-size: 16px; line-height: 25px;
  }
  .postcard--back .name-band { top: 309px; width: 185px; }
  .contact-email { position: absolute; font-size: 14px; }
  .postcard--back .contact-email { left: 34px; top: 341px; }

  /* ---------- front side ---------- */
  .postcard--front { left: 516px; top: 435px; width: 660px; height: 510px; }
  .front-wash {
    position: absolute; inset: 0;
    background: linear-gradient(135deg, #e4f2f8 0%, #ffffff 25%, #ffffff 100%);
  }
  .splash-art {
    position: absolute; left: 120px; top: 150px; width: 320px; height: 360px;
    background:
      radial-gradient(ellipse 35% 30% at 40% 15%, rgba(90,150,220,.45), rgba(255,255,255,0) 70%),
      radial-gradient(ellipse 40% 35% at 55% 50%, rgba(170,80,190,.45), rgba(255,255,255,0) 70%),
      radial-gradient(ellipse 35% 30% at 30% 75%, rgba(230,90,160,.35), rgba(255,255,255,0) 70%),
      radial-gradient(ellipse 30% 20% at 25% 95%, rgba(200,220,120,.3), rgba(255,255,255,0) 70%);
  }
  .front-portrait {
    position: absolute; right: 0; top: 0; width: 315px; height: 510px;
    background:
      radial-gradient(ellipse 45% 35% at 50% 38%, var(--photo-light), rgba(230,230,230,0) 75%),
      linear-gradient(180deg, #d6d6d6 0%, var(--photo-mid) 55%, var(--photo-dark) 100%);
  }
  .portrait-caption {
    position: absolute; right: 33px; bottom: 24px;
    font-family: "Cinzel", Georgia, serif; font-size: 21px; color: #fff; letter-spacing: .02em;
  }
  .postcard--front .brand-mark { left: 50px; top: 75px; font-size: 19px; }
  .headline {
    position: absolute; left: 222px; top: 64px;
    font-family: "Cinzel", Georgia, serif; font-weight: 400; white-space: nowrap;
  }
  .headline__soft { font-size: 23px; color: var(--ink); }
  .headline__bold { font-size: 38px; font-weight: 600; color: var(--magenta); margin-left: 6px; }
  .front-intro {
    position: absolute; left: 35px; top: 136px; width: 390px;
    font-size: 11.6px; line-height: 16.5px;
  }
  .quote-mark {
    position: absolute; left: 32px; top: 232px;
    font-family: Georgia, serif; font-weight: 700; font-size: 92px; line-height: 1; color: var(--ink);
  }
  .quote-text {
    position: absolute; left: 90px; top: 228px; width: 290px;
    font-size: 15.6px; line-height: 21.7px;
  }
  .postcard--front .name-band { top: 396px; width: 185px; padding-left: 35px; }
  .postcard--front .contact-email { left: 35px; top: 429px; }
</style>
</head>
<body>

<section class="postcard postcard--back" aria-label="Postcard back">
  <div class="back-portrait" role="img" aria-label="Faded portrait photo of the designer"></div>
  <div class="stamp-box"></div>
  <div class="brand-mark"><span class="brand-mark__dot"></span>Solene Vara</div>
  <p class="back-bio">Dr. Lena’s jewelry has been worn by stylists, designers, high profile TV personalities and anchors, as well as people who just want to look good and feel beautiful.</p>
  <div class="name-band">Dr. Lena Marlowe</div>
  <p class="contact-email">email: info@drlenamarlowe.com</p>
</section>

<section class="postcard postcard--front" aria-label="Postcard front">
  <div class="front-wash"></div>
  <div class="splash-art" role="img" aria-label="Colourful abstract splash artwork in blue, violet and pink"></div>
  <div class="front-portrait" role="img" aria-label="Black and white portrait photo of the designer"></div>
  <p class="portrait-caption">DR. LENA</p>
  <div class="brand-mark"><span class="brand-mark__dot"></span>Solene Vara</div>
  <h1 class="headline"><span class="headline__soft">DREAM</span><span class="headline__bold">BIG</span></h1>
  <p class="front-intro">These pieces are based on the bold and dramatic costume pieces of the 60’s and 70’s. Everyone deserves to feel Glamorous and beautiful. This collection is a great way to step into your most stunning self.</p>
  <span class="quote-mark" aria-hidden="true">“</span>
  <blockquote class="quote-text">It’s my goal to make every woman feel like her very best self, so she can go out into the world to sparkle and shine. To create a line of jewelry that’s both beautiful and purposeful is truly a dream come true.”</blockquote>
  <div class="name-band">Dr. Lena Marlowe</div>
  <p class="contact-email">email: lena@drlenamarlowe.com</p>
</section>

</body>
</html>
```